Corvane Business Cards

Front of business card will have logo, name, address, & telephone number. Back of card will have a list of services provided - Roads, Substation Pads, Temporary Pads, Site Pads, Land Leveling, Powerline Row Cleaning, Land Clearing, Gates, Fencing, Construction Entrances, Excavation, Trenching, Underground Utilities, Directional Boring, Pile Driving. We are a construction company that uses heavy equipment like bulldozers, motor graders/blades, dump trucks, backhoes, hydro axes, & skid loaders. We build roads, pads, & install electric utility lines & waterlines underground. This logo is new. The word "Construction" can be smaller as uploaded 2 example edited logos. We will be using this card design for many employees.
Target Market(s)
Industrial Electric Powerline, Wind Turbine, Solar Panel, & Water Utility companies.
Contact Information for Business Card
Name/Position - Dwayne Halster - Owner
Address: 4875 FM 309
Harlow Creek, KS 67412
Phone number - (620) 482-5096

```html
<!DOCTYPE html>
<html lang="en">
<head>
<meta charset="utf-8">
<title>Corvane Construction Business Cards</title>
<link href="https://fonts.googleapis.com/css2?family=Marcellus&family=Montserrat:wght@400;600;700&display=swap" rel="stylesheet">
<style>
  :root {
    --maroon: #3d0d19;
    --paper: #ffffff;
    --backdrop: #e6e3e3;
    --ink: #3d0d19;
  }
  * { box-sizing: border-box; margin: 0; padding: 0; }
  html, body { width: 1200px; height: 852px; overflow: hidden; }
  body {
    background: var(--backdrop);
    display: flex;
    flex-direction: column;
    align-items: center;
    justify-content: center;
    gap: 14px;
    font-family: "Montserrat", sans-serif;
  }
  .card {
    width: 720px;
    height: 408px;
    border-radius: 22px;
    position: relative;
    box-shadow: 0 6px 18px rgba(0,0,0,.18);
  }
  .wordmark {
    font-family: "Marcellus", serif;
    text-align: center;
    line-height: 1;
  }
  .wordmark__name {
    display: inline-flex;
    align-items: center;
    gap: 10px;
    font-size: 34px;
    letter-spacing: 3px;
  }
  .wordmark__dot {
    width: 12px; height: 12px; border-radius: 50%;
    background: currentColor;
  }
  .wordmark__tagline {
    display: block;
    font-size: 50px;
    letter-spacing: 1px;
    margin-top: 6px;
  }

  /* services side */
  .card--services { background: var(--maroon); color: var(--paper); }
  .card--services .wordmark { position: absolute; top: 48px; left: 0; right: 0; }
  .services {
    position: absolute;
    left: 44px; right: 36px; bottom: 44px;
    display: grid;
    grid-template-columns: 150px 190px 1fr;
    gap: 22px;
    font-size: 16px;
    align-items: end;
  }
  .services__title { font-weight: 700; font-size: 16px; margin-bottom: 2px; }
  .services ul { list-style: none; }
  .services li {
    line-height: 1.5;
    padding-left: 18px;
    position: relative;
    white-space: nowrap;
  }
  .services li::before {
    content: ""; position: absolute; left: 0; top: 9px;
    width: 7px; height: 7px; border-radius: 50%; background: var(--paper);
  }

  /* contact side */
  .card--contact { background: var(--paper); color: var(--ink); text-align: center; }
  .card--contact .wordmark { padding-top: 54px; }
  .card--contact .wordmark__name { font-size: 28px; }
  .card--contact .wordmark__tagline { font-size: 40px; }
  .rule { width: 360px; height: 2px; background: var(--ink); margin: 0 auto; }
  .rule--top { margin-top: 16px; }
  .contact__name { font-weight: 700; font-size: 21px; margin-top: 16px; letter-spacing: .5px; }
  .contact__role { font-size: 15px; margin-top: 2px; margin-bottom: 24px; }
  .contact__details { font-size: 18px; line-height: 1.6; margin-top: 20px; }
</style>
</head>
<body>
  <section class="card card--services">
    <div class="wordmark">
      <span class="wordmark__name"><span class="wordmark__dot"></span>CORVANE</span>
      <span class="wordmark__tagline">CONSTRUCTION</span>
    </div>
    <div class="services">
      <div>
        <p class="services__title">Services:</p>
        <ul>
          <li>Roads</li>
          <li>Site Pads</li>
          <li>Gates</li>
          <li>Fencing</li>
        </ul>
      </div>
      <ul>
        <li>Trenching</li>
        <li>Temporary Pads</li>
        <li>Land Leveling</li>
        <li>Land Clearing</li>
        <li>Substation Pads</li>
      </ul>
      <ul>
        <li>Powerline Row Cleaning</li>
        <li>Construction Entrances</li>
        <li>Excavation</li>
        <li>Underground Utilities</li>
        <li>Directional Boring, Pile Driving</li>
      </ul>
    </div>
  </section>

  <section class="card card--contact">
    <div class="wordmark">
      <span class="wordmark__name"><span class="wordmark__dot"></span>CORVANE</span>
      <span class="wordmark__tagline">CONSTRUCTION</span>
    </div>
    <div class="rule rule--top"></div>
    <p class="contact__name">DWAYNE HALSTER</p>
    <p class="contact__role">owner</p>
    <div class="rule"></div>
    <p class="contact__details">(620) 482-5096<br>4875 FM 309 Harlow Creek, KS 67412</p>
  </section>
</body>
</html>
```